Business card for my new company (Accounting firm)

I need a business card for my new business Brightwell Advisory and Ledger SA. Our services are accounting, tax, audit and financial management. Our customers are small companies, start-ups and new companies. The final design has to show financial security, trust and growth. Please find our logo attached to the business card. Text for the business card: Brightwell Advisory and Ledger SA Tomas Varenholt Director and Founder Certified Accountant Tel. 022 418 57 34 tv@clairevalconseil.ch www.clairevalconseil.ch Rue des Vergières 27 1201 Geneva
Target Market(s)
Our customers are small companies, start-ups and new companies.
Industry/Entity Type
Finance And Accounting
Contact Information for Business Card
Claireval Conseil et Comptes SA
Tomas Varenholt
Directeur et Fondateur
Expert-comptable diplômé
Tél. 022 418 57 34
tv@clairevalconseil.ch
www.clairevalconseil.ch
Rue des Vergières 27
1201 Genève

```html
<!DOCTYPE html>
<html lang="fr">
<head>
<meta charset="utf-8">
<title>Claireval Conseil et Comptes – Carte de visite</title>
<link rel="stylesheet" href="https://fonts.googleapis.com/css2?family=Roboto:wght@400;700&display=swap">
<style>
  :root {
    --page-bg: #e4e5e7;
    --blue-light: #2a9fd6;
    --blue-mid: #2287c0;
    --blue-deep: #1b6a9e;
    --ink: #3a3a3c;
    --rule: #353538;
    --paper: #f7f7f7;
    --white: #ffffff;
  }
  * { margin: 0; padding: 0; box-sizing: border-box; }
  html, body {
    width: 1200px; height: 726px; overflow: hidden;
    background: var(--page-bg);
    font-family: "Roboto", Arial, sans-serif;
  }
  .sheet {
    position: relative; width: 1200px; height: 726px;
    display: flex; align-items: center; justify-content: center; gap: 40px;
  }
  .card {
    position: relative; width: 530px; height: 303px; overflow: hidden;
    box-shadow: 0 6px 18px rgba(0,0,0,0.12);
  }
  /* Front */
  .card--front {
    background: linear-gradient(160deg, var(--blue-light) 0%, var(--blue-mid) 50%, var(--blue-deep) 100%);
    color: var(--white);
    display: flex; flex-direction: column; align-items: center; justify-content: center;
  }
  .brand-name { font-weight: 700; text-align: center; line-height: 1.1; }
  .card--front .brand-name { font-size: 40px; color: var(--white); }
  .card--front .website {
    margin-top: 26px; font-size: 15px; font-weight: 700; letter-spacing: 0.3px;
  }
  /* Back */
  .card--back { background: var(--paper); color: var(--ink); }
  .header-band {
    position: absolute; left: 0; top: 0; width: 100%; height: 96px;
    background: linear-gradient(90deg, var(--blue-light), var(--blue-deep));
    border-bottom: 4px solid var(--rule);
  }
  .holder {
    position: absolute; right: 24px; top: 20px; text-align: right; color: var(--white);
  }
  .holder__name { font-size: 18px; font-weight: 700; }
  .holder__role { font-size: 11px; line-height: 1.35; margin-top: 3px; }
  .contact {
    position: absolute; right: 24px; top: 126px; text-align: right;
    font-size: 12.5px; line-height: 1.45;
  }
  .contact__address { margin-bottom: 12px; }
  .contact__row { display: flex; align-items: center; justify-content: flex-end; gap: 7px; }
  .contact__icon { width: 12px; height: 12px; flex: none; }
  .card--back .brand-name {
    position: absolute; left: 40px; top: 200px; text-align: left;
    font-size: 30px; color: var(--ink);
  }
</style>
</head>
<body>
<main class="sheet">
  <section class="card card--front" aria-label="Recto">
    <div class="brand-name">Claireval<br>Conseil et Comptes</div>
    <div class="website">www.clairevalconseil.ch</div>
  </section>

  <section class="card card--back" aria-label="Verso">
    <div class="header-band" aria-hidden="true"></div>

    <div class="holder">
      <div class="holder__name">Tomas Varenholt</div>
      <div class="holder__role">Directeur et Fondateur<br>Expert-comptable diplômé</div>
    </div>

    <div class="contact">
      <div class="contact__address">Rue des Vergières 27<br>1201 Genève</div>
      <div class="contact__row">022 418 57 34
        <svg class="contact__icon" viewBox="0 0 12 12" aria-hidden="true"><path d="M2.5 1 L4.5 1 L5 3.5 L3.8 4.4 C4.4 5.8 5.8 7.4 7.6 8.2 L8.5 7 L11 7.5 L11 9.5 C11 10.3 10.3 11 9.5 11 C5 11 1 7 1 2.5 C1 1.7 1.7 1 2.5 1 Z" fill="var(--blue-mid)"/></svg>
      </div>
      <div class="contact__row">tv@clairevalconseil.ch
        <svg class="contact__icon" viewBox="0 0 12 12" aria-hidden="true"><rect x="0.5" y="2.5" width="11" height="7.5" rx="1" fill="var(--blue-mid)"/><path d="M1 3 L6 7 L11 3" stroke="#fff" stroke-width="1" fill="none"/></svg>
      </div>
      <div class="contact__row">www.clairevalconseil.ch
        <svg class="contact__icon" viewBox="0 0 12 12" aria-hidden="true"><circle cx="6" cy="6" r="5.3" fill="var(--blue-mid)"/><path d="M0.8 6 H11.2 M6 0.8 C3.5 3.5 3.5 8.5 6 11.2 M6 0.8 C8.5 3.5 8.5 8.5 6 11.2" stroke="#fff" stroke-width="0.8" fill="none"/></svg>
      </div>
    </div>

    <div class="brand-name">Claireval<br>Conseil et Comptes</div>
  </section>
</main>
</body>
</html>
```